Summer Time Cleaning!

Vent Haven Partners Inc. is a family owned business since 2007, RFBLO certified techs, using the most advanced equipment offered in the field. Would like to attract as many customers as possible to bring in a swarm of work during our slow time.please print on jumbo size post card.

Target Market(s)

Main line area homes worth $500,000+

Industry/Entity Type

Residential

Requirements
Must have
• Would like special on Air duct cleaning: Air Duct Cleaning Special- Full home power air duct cleaning only $300.00 offer expires August 29th. Dryer Vent Cleaning Special- Any dryer vent cleaning services includes a FREE lint alert system!
Nice to have
• Would like bright colors, need the post card to really stand out!

```html
<!DOCTYPE html>
<html lang="en">
<head>
<meta charset="utf-8">
<title>Vent Haven Partners – Summer Postcard</title>
<link rel="stylesheet" href="https://fonts.googleapis.com/css2?family=Bebas+Neue&display=swap">
<style>
  :root {
    --bg-light: #f7f7f6;
    --bg-soft: #ecebea;
    --ink-grey: #ececec;
    --ink-grey-shadow: #8a8a8a;
    --brand-teal: #4cc6d4;
    --accent-yellow: #f5c92a;
    --band-light: #a9e3f2;
    --band-blue: #1aa1dc;
    --band-deep: #0f84c4;
    --ink-deep: #0d5f8f;
    --white: #ffffff;
    --photo-light: #f1ece7;
    --photo-warm: #e6d6ca;
  }
  * { margin: 0; padding: 0; box-sizing: border-box; }
  html, body { width: 1200px; height: 662px; overflow: hidden; background: var(--bg-light); }
  .postcard {
    position: relative;
    width: 1200px;
    height: 662px;
    overflow: hidden;
    background: linear-gradient(90deg, var(--bg-light) 0%, #fbfbfa 45%, var(--bg-soft) 100%);
    font-family: "Bebas Neue", sans-serif;
  }
  .hero-photo {
    position: absolute;
    left: 640px; top: 0;
    width: 560px; height: 600px;
    background: linear-gradient(90deg, rgba(247,247,246,1) 0%, var(--photo-light) 30%, var(--photo-warm) 100%);
  }
  .brand-name {
    position: absolute;
    left: 48px; top: 30px;
    font-size: 96px;
    font-weight: 400;
    line-height: 0.92;
    color: var(--brand-teal);
    letter-spacing: 1px;
  }
  .pitch {
    position: absolute;
    left: 140px; top: 232px;
    font-size: 38px;
    line-height: 1.06;
    letter-spacing: 0.5px;
    text-shadow: 1px 2px 0 var(--ink-grey-shadow);
  }
  .pitch-line { display: block; color: var(--ink-grey); }
  .pitch-line--accent { color: var(--accent-yellow); }
  .specials {
    position: absolute;
    left: 720px; top: 44px;
    width: 440px;
    color: var(--ink-deep);
  }
  .special + .special { margin-top: 22px; }
  .special-title {
    font-size: 40px;
    line-height: 1;
    font-weight: 400;
    color: var(--brand-teal);
    letter-spacing: 0.5px;
  }
  .special-text {
    font-size: 29px;
    line-height: 1.08;
    letter-spacing: 0.4px;
    margin-top: 4px;
  }
  .special-price { color: var(--band-blue); }
  .band { position: absolute; left: 0; top: 0; width: 1200px; height: 662px; }
  .badge {
    position: absolute;
    border-radius: 50%;
    border: 7px solid var(--white);
    box-shadow: 0 3px 10px rgba(0,0,0,0.25);
    overflow: hidden;
  }
  .badge--result {
    left: 36px; top: 402px; width: 186px; height: 186px;
    background: linear-gradient(90deg, #6f7275 0%, #9ea2a4 40%, #d8d6cf 60%, #eeece5 100%);
  }
  .badge-label {
    position: absolute;
    bottom: 42px; width: 100%;
    text-align: center;
    font-size: 24px;
    color: var(--white);
    letter-spacing: 0.5px;
    text-shadow: 1px 1px 2px #000;
  }
  .badge--cert {
    left: 255px; top: 458px; width: 180px; height: 180px;
    background: var(--white);
  }
  .badge-mark {
    position: absolute; left: 50%; top: 50%;
    width: 112px; height: 112px;
    margin: -56px 0 0 -56px;
    border-radius: 50%;
    background: var(--band-light);
  }
  .call-to-action {
    position: absolute;
    left: 477px; top: 592px;
    display: flex; align-items: center; gap: 16px;
    font-size: 46px;
    line-height: 1;
    letter-spacing: 0.5px;
  }
  .cta-label { color: var(--accent-yellow); }
  .cta-phone { color: var(--white); display: flex; align-items: center; gap: 8px; }
  .phone-icon { width: 34px; height: 34px; }
</style>
</head>
<body>
<main class="postcard">
  <div class="hero-photo" role="img" aria-label="Lifestyle photo of a homeowner affected by dusty indoor air"></div>

  <h1 class="brand-name">Vent Haven<br>Partners</h1>

  <p class="pitch">
    <span class="pitch-line">Dont waste your money on cheap</span>
    <span class="pitch-line">imitators using impoper methods</span>
    <span class="pitch-line pitch-line--accent">Our methods are not only affordable</span>
    <span class="pitch-line pitch-line--accent">but done right the first time!</span>
  </p>

  <section class="specials">
    <div class="special">
      <h2 class="special-title">Air Duct Cleaning Special</h2>
      <p class="special-text">Full home power air duct cleaning only <span class="special-price">$300.00</span><br>Offer expires August 29th</p>
    </div>
    <div class="special">
      <h2 class="special-title">Dryer Vent Cleaning Special</h2>
      <p class="special-text">Any dryer vent cleaning service includes a <span class="special-price">free lint alert system!</span></p>
    </div>
  </section>

  <svg class="band" viewBox="0 0 1200 662" aria-hidden="true">
    <path d="M0 372 C 300 440, 700 560, 1200 545 L1200 662 L0 662 Z" fill="var(--band-light)"/>
    <path d="M0 400 C 320 470, 720 590, 1200 575 L1200 662 L0 662 Z" fill="var(--band-blue)"/>
    <path d="M0 600 C 400 630, 800 650, 1200 630 L1200 662 L0 662 Z" fill="var(--band-deep)" opacity="0.5"/>
  </svg>

  <div class="badge badge--result" role="img" aria-label="Photo of a duct interior before and after cleaning">
    <span class="badge-label">BEFORE AFTER</span>
  </div>
  <div class="badge badge--cert" role="img" aria-label="Certification badge">
    <span class="badge-mark"></span>
  </div>

  <div class="call-to-action">
    <span class="cta-label">Call for a free estimate</span>
    <span class="cta-phone">
      <svg class="phone-icon" viewBox="0 0 34 34" aria-hidden="true">
        <circle cx="17" cy="17" r="16" fill="var(--white)"/>
        <path d="M11.5 8.5c1-.6 2.2-.3 2.8.7l1.6 2.6c.5.9.3 2-.5 2.6l-1.2.9c.9 2 2.4 3.6 4.4 4.6l.9-1.2c.6-.8 1.7-1 2.6-.5l2.6 1.6c1 .6 1.3 1.8.7 2.8l-.8 1.2c-.8 1.3-2.4 1.9-3.9 1.4C14.5 23.5 10.4 19.4 8.6 13.3c-.5-1.5.1-3.1 1.4-3.9z" fill="var(--band-blue)"/>
      </svg>
      555-014-2290
    </span>
  </div>
</main>
</body>
</html>
```